Business Card Design

We are a commercial real estate brokerage in San Francisco, leasing office buildings downtown.
I would like a clean, elegant look. Simple but powerful .

Industry/Entity Type

Business

Contact Information for Business Card

Derek Holloway
lic# 07258143
415.555.0172
derek@velt-commercial.example
velt-commercial.example

```html
<!DOCTYPE html>
<html lang="en">
<head>
<meta charset="utf-8">
<title>Velt Commercial – Business Card</title>
<link rel="stylesheet" href="https://fonts.googleapis.com/css2?family=Source+Sans+3:wght@400;600&display=swap">
<style>
  :root {
    --backdrop: #8e8e8e;
    --card: #e8e8eb;
    --ink: #333438;
    --slate: #5d6b8c;
    --rule: #2c2c2e;
    --skyline-tint: #d9d9dd;
  }
  * { margin: 0; padding: 0; box-sizing: border-box; }
  html, body {
    width: 1105px; height: 1200px; overflow: hidden;
    background: var(--backdrop);
    font-family: "Source Sans 3", "Helvetica Neue", Arial, sans-serif;
  }
  .card {
    position: absolute; left: 180px;
    width: 746px; height: 426px;
    background: var(--card);
    overflow: hidden;
  }
  .card--front { top: 118px; }
  .card--back { top: 636px; }

  .skyline-backdrop {
    position: absolute; left: 409px; top: 8px;
    width: 337px; height: 418px;
    background: linear-gradient(180deg, rgba(217,217,221,0) 0%, var(--skyline-tint) 30%, var(--skyline-tint) 100%);
    opacity: 0.7;
  }

  .divider {
    position: absolute; left: 181px; top: 65px;
    width: 2px; height: 302px; background: var(--rule);
  }

  .brand {
    position: absolute;
    color: var(--slate);
    font-weight: 600;
    line-height: 0.95;
    letter-spacing: 0.5px;
  }
  .brand--front { left: 198px; top: 74px; font-size: 38px; }
  .brand__line { display: block; }

  .contact {
    position: absolute; left: 140px; top: 188px;
    list-style: none;
  }
  .contact__row {
    display: flex; align-items: center;
    height: 28px;
  }
  .contact__icon { width: 22px; height: 22px; margin-right: 40px; flex: none; }
  .contact__icon--blank { visibility: hidden; }
  .contact__text { font-size: 19px; color: var(--ink); }
  .contact__name { font-size: 27px; color: var(--slate); font-weight: 600; }
  .contact__row--name { height: 36px; }
  .contact__gap { height: 18px; }

  .brand--back {
    left: 0; right: 0; top: 170px;
    text-align: center; font-size: 44px;
  }
</style>
</head>
<body>
  <section class="card card--front" aria-label="Business card front">
    <div class="skyline-backdrop" role="img" aria-label="Faint illustration of downtown office towers"></div>
    <div class="divider"></div>
    <div class="brand brand--front">
      <span class="brand__line">VELT</span>
      <span class="brand__line">COMMERCIAL</span>
    </div>
    <ul class="contact">
      <li class="contact__row contact__row--name">
        <svg class="contact__icon" viewBox="0 0 24 24" fill="var(--slate)" aria-hidden="true"><circle cx="12" cy="8" r="5"/><path d="M3 22c0-5 4-8 9-8s9 3 9 8z"/></svg>
        <span class="contact__name">Derek Holloway</span>
      </li>
      <li class="contact__row">
        <svg class="contact__icon contact__icon--blank" viewBox="0 0 24 24" aria-hidden="true"></svg>
        <span class="contact__text">lic# 07258143</span>
      </li>
      <li class="contact__gap"></li>
      <li class="contact__row">
        <svg class="contact__icon" viewBox="0 0 24 24" fill="var(--slate)" aria-hidden="true"><path d="M6.6 10.8a15 15 0 0 0 6.6 6.6l2.2-2.2c.3-.3.7-.4 1-.2 1.1.4 2.3.6 3.6.6.6 0 1 .4 1 1V20c0 .6-.4 1-1 1A17 17 0 0 1 3 4c0-.6.4-1 1-1h3.5c.6 0 1 .4 1 1 0 1.3.2 2.5.6 3.6.1.3 0 .7-.2 1z"/></svg>
        <span class="contact__text">415.555.0172</span>
      </li>
      <li class="contact__row">
        <svg class="contact__icon" viewBox="0 0 24 24" aria-hidden="true"><rect x="3" y="6" width="18" height="12" rx="1.5" fill="var(--slate)"/><path d="M3.5 7l8.5 6 8.5-6" fill="none" stroke="var(--card)" stroke-width="1.6"/></svg>
        <span class="contact__text">derek@velt-commercial.example</span>
      </li>
      <li class="contact__row">
        <svg class="contact__icon" viewBox="0 0 24 24" aria-hidden="true"><circle cx="12" cy="12" r="9" fill="var(--slate)"/><path d="M3 12h18M12 3c3 3 3 15 0 18M12 3c-3 3-3 15 0 18" fill="none" stroke="var(--card)" stroke-width="1.3"/></svg>
        <span class="contact__text">velt-commercial.example</span>
      </li>
    </ul>
  </section>

  <section class="card card--back" aria-label="Business card back">
    <div class="brand brand--back">
      <span class="brand__line">VELT</span>
      <span class="brand__line">COMMERCIAL</span>
    </div>
  </section>
</body>
</html>
```